Automotive component supplier needs a business card design

We need a business card design for our company called Velran Global Components Ltd based in the UK. We are a supplier of interior and exterior components to premium car manufacturers such as Corvel Ashby, Hadley Fenn, Marquist and Tavarelli. We would like to see a modern business card design that uses the colour blue.

Target Market(s)

Premium automotive car manufacturers.

Industry/Entity Type

Automotive

Contact Information for Business Card

Company Name : Velran Global Components Limited
Address: 17 Marlow Yard, Upper Heath, Warwick, CV31 8QL, United Kingdom
Web Address : www.velrancomponents-example.co.uk

Font styles to use
Other font styles liked:
• Helvetica

Colors
3176b5
0255a3
85acd3
cfdeed
cee9f5
85cae6
34a6d7
0692cd
9bcb3c

Requirements
Must have
• Clear company logo and a mixture of blue colours.
Nice to have
• A high quality modern image.
Should not have
• Multiple colours.

```html
<!DOCTYPE html>
<html lang="en">
<head>
<meta charset="utf-8">
<title>Velran Global Components – Business Card</title>
<link rel="stylesheet" href="https://fonts.googleapis.com/css2?family=PT+Sans:wght@400;700&display=swap">
<style>
  :root {
    --backdrop: #2b2b2b;
    --card-white: #ffffff;
    --brand-blue: #0692cd;
    --band-blue: #0b8fcd;
    --accent-green: #9bcb3c;
    --faint-blue: #eef6fb;
    --ink-grey: #4a4a4a;
  }
  * { margin: 0; padding: 0; box-sizing: border-box; }
  html, body {
    width: 1200px; height: 987px; overflow: hidden;
    background: var(--backdrop);
    font-family: "PT Sans", Helvetica, Arial, sans-serif;
  }
  .canvas { position: relative; width: 1200px; height: 987px; }

  .card {
    position: absolute; left: 293px; width: 615px; height: 352px;
    background: var(--card-white); overflow: hidden;
  }
  .card--front { top: 130px; }
  .card--back  { top: 505px; }

  .wordmark { position: absolute; color: var(--brand-blue); font-weight: 700; line-height: 1; }
  .wordmark__name { display: block; letter-spacing: 2px; }
  .wordmark__sub  { display: block; letter-spacing: 0.6px; }

  .card--front .wordmark { left: 34px; top: 50px; }
  .card--front .wordmark__name { font-size: 56px; }
  .card--front .wordmark__sub  { font-size: 15.5px; margin-top: 4px; }

  .contact-band {
    position: absolute; left: 0; top: 171px; width: 100%; height: 160px;
    background: var(--band-blue); color: var(--card-white);
    font-size: 15.5px; line-height: 21px;
  }
  .accent-square {
    position: absolute; right: 2px; top: 170px; width: 31px; height: 23px;
    background: var(--accent-green); border-radius: 4px; border: 2px solid var(--card-white);
  }
  .address { position: absolute; left: 34px; top: 22px; }
  .contact-left  { position: absolute; left: 34px; top: 98px; }
  .contact-right { position: absolute; right: 34px; top: 98px; text-align: right; }
  .person { position: absolute; right: 34px; top: 38px; text-align: right; }
  .person__name { font-size: 21px; font-weight: 700; letter-spacing: 0.5px; line-height: 24px; }
  .person__role { font-size: 15.5px; }
  .contact-line { display: block; line-height: 25px; }
  .contact-line strong { font-weight: 700; }

  .back-field {
    position: absolute; inset: 0; background: var(--faint-blue);
  }
  .card--back .wordmark { left: 0; right: 0; top: 134px; text-align: center; }
  .card--back .wordmark__name { font-size: 74px; }
  .card--back .wordmark__sub  { font-size: 18px; margin-top: 6px; }
  .back-url {
    position: absolute; left: 0; right: 0; top: 290px; text-align: center;
    color: var(--ink-grey); font-size: 15px; letter-spacing: 5px;
  }
</style>
</head>
<body>
<main class="canvas">

  <section class="card card--front">
    <div class="wordmark">
      <span class="wordmark__name">VELRAN</span>
      <span class="wordmark__sub">GLOBAL COMPONENTS</span>
    </div>

    <div class="contact-band">
      <address class="address" style="font-style:normal">
        17 Marlow Yard, Upper Heath<br>
        Warwick, CV31 8QL<br>
        United Kingdom
      </address>
      <div class="person">
        <div class="person__name">DANIEL MERCER</div>
        <div class="person__role">CEO/Founder</div>
      </div>
      <div class="contact-left">
        <span class="contact-line"><strong>Phone:</strong> 689 555 0142</span>
        <span class="contact-line">www.velrancomponents-example.co.uk</span>
      </div>
      <div class="contact-right">
        <span class="contact-line"><strong>Mobile:</strong> 836 555 0178</span>
        <span class="contact-line">daniel@velrancomponents-example.co.uk</span>
      </div>
    </div>
    <div class="accent-square"></div>
  </section>

  <section class="card card--back">
    <div class="back-field" role="img" aria-label="Faint repeating brand-name pattern in pale blue"></div>
    <div class="wordmark">
      <span class="wordmark__name">VELRAN</span>
      <span class="wordmark__sub">GLOBAL COMPONENTS</span>
    </div>
    <div class="back-url">www.velrancomponents-example.co.uk</div>
  </section>

</main>
</body>
</html>
```